Modern, clean and professional Wordpress design for a safety training company!

We are currently in the process of creating a new website for our business. We have hired a website developer and the main structure of our new Wordpress site is complete. We now need an overall design plan for the site. We need a very clean, professional and easy to follow website. Most of our website visitors only spend about 30-45 secs on our sites "shopping " so it is imperative that we have a strong Home Page.
Our company specializes in CPR and First Aid Certification Classes to businesses and individuals throughout Northern California. We provide these certifications two ways: ONSITE-We come to you, and HOSTED-we offer weekly classes at our 2 locations.
Our design needs to use the general green and blue colors of our logo. But we also like white.
The final design MUST communicate a legitimate, trustworthy and professional business. Our industry is VERY competitive and we need to STAND OUT.
Currently, the NEW website that we need a new design for is www.LifelineDrillWorks.com
Our old website is www.RescuePrepValleyHub.com and we really do like the design of this website, but we just needed a Wordpress site for SEO purposes.
These are 3 websites that we really:
http://morvaliontech.com/
http://www.tralbex.com/
https://www.plivant.com/
I have attached our Logo and other images if you need to use them but looking at the current two sites will be you best help.
Target Market(s)
1) Large businesses and industries that are looking for a company to provide ONSITE safety training classes at their office or place of work.
2) Individuals that need certifications for their jobs and other needs. These individuals are looking for a legitimate, trustworthy and professional environment to complete their training class.

```html
<!DOCTYPE html>
<html lang="en">
<head>
<meta charset="utf-8">
<title>Summit Safety Academy – CPR &amp; First Aid Certification</title>
<link rel="stylesheet" href="https://fonts.googleapis.com/css2?family=Roboto:wght@400;500&family=Open+Sans:wght@400;600&family=Oswald:wght@500&family=Lobster&display=swap">
<style>
:root{
  --blue:#1f2a7c;
  --green:#6ea52c;
  --green-light:#7cb335;
  --text:#333;
  --muted:#555;
  --bg:#eeeeee;
  --panel:#f0f0f0;
  --footer:#2b2b2b;
  --footer-text:#bdbdbd;
  --white:#fff;
}
*{margin:0;padding:0;box-sizing:border-box}
html,body{width:701px;height:1200px;overflow:hidden;background:var(--bg)}
body{position:relative;font-family:"Open Sans",sans-serif;color:var(--text)}
.page{position:absolute;left:58px;top:10px;width:586px;height:1176px;background:var(--white);box-shadow:0 0 3px rgba(0,0,0,.15);overflow:hidden}
.abs{position:absolute}
/* header */
.brand{left:16px;top:22px;display:flex;align-items:center;gap:6px}
.brand-mark{width:22px;height:22px;border-radius:50%;background:var(--green)}
.brand-name{font-family:"Roboto",sans-serif;font-weight:500;font-size:14px;color:var(--blue);letter-spacing:.3px}
.phone-icon{left:322px;top:23px}
.contact-top{left:356px;top:22px;font-family:"Roboto",sans-serif}
.contact-top .ph{font-size:11px;color:var(--blue)}
.contact-top .em{font-size:8px;color:var(--muted);margin-top:4px}
.search{left:468px;top:25px;width:103px;height:22px;border:1px solid #ddd;font-size:7px;color:#555;padding:6px 8px}
.search svg{position:absolute;right:6px;top:6px}
/* nav */
.nav{left:0;top:69px;width:586px;height:34px;background:var(--blue);border-bottom:2px solid var(--green);display:flex;align-items:center;justify-content:space-between;padding:0 14px;font-family:"Roboto",sans-serif;font-size:9.5px;color:var(--white)}
/* sidebar */
.appt{left:0;top:105px;width:153px;height:284px;background:var(--panel);padding:15px 10px}
.appt h2{font-family:"Roboto",sans-serif;font-weight:400;font-size:10.5px;color:var(--green);padding-bottom:9px;border-bottom:1px solid #ddd}
.appt address{font-style:normal;font-size:7.5px;line-height:13px;margin:10px 0 7px 0}
.field{height:24px;background:var(--white);border:1px solid #e4e4e4;margin-bottom:6px;font-size:6.5px;color:#555;padding:7px 8px}
.appt .btn{height:25px;background:var(--green);color:var(--white);font-size:7px;text-align:center;line-height:25px;margin-top:8px}
/* hero */
.hero{left:153px;top:105px;width:433px;height:284px;background:linear-gradient(135deg,#d9dee3 0%,#b8c1c8 35%,#8a7a6e 70%,#5c4c44 100%)}
.hero-title{right:32px;top:160px;text-align:right;font-family:"Oswald",sans-serif;color:var(--white);line-height:1}
.hero-title .l1{font-size:42px}
.hero-title .l2{font-size:17px;margin-top:2px}
.arrows{left:338px;top:248px;display:flex;gap:4px}
.arrows span{width:18px;height:18px;border:1px solid rgba(255,255,255,.7);border-radius:50%}
/* welcome */
.welcome{left:0;top:405px;width:586px;text-align:center}
.welcome h1{font-family:"Roboto",sans-serif;font-weight:500;font-size:19px;color:#333}
.welcome h1 span{color:var(--blue)}
.welcome p{font-size:6.3px;line-height:12.5px;color:var(--muted);width:460px;margin:8px auto 0}
.card{top:484px;width:174px}
.card .photo{height:108px}
.card h3{font-family:"Roboto",sans-serif;font-weight:400;font-size:8.5px;margin-top:13px}
.card p{font-size:6.2px;line-height:12px;color:var(--muted);margin-top:6px}
/* specialities */
.spec{left:14px;top:673px;width:557px;height:83px;background:var(--green-light);border-radius:3px;overflow:hidden}
.spec .photo{position:absolute;left:0;top:0;width:180px;height:83px;background:linear-gradient(90deg,#cfc3bc 0%,#b9aca5 60%,var(--green-light) 100%)}
.spec .script{position:absolute;left:166px;top:10px;font-family:"Lobster",cursive;color:#fff;font-size:26px;line-height:28px}
.spec .script span{display:block;color:#333;font-size:26px}
.spec .col{position:absolute;top:10px;color:var(--white);font-family:"Roboto",sans-serif}
.spec .col b{display:block;font-weight:400;font-size:17px;margin-bottom:5px}
.spec .col div{font-size:8.5px;line-height:14px}
.spec .sep{position:absolute;left:437px;top:10px;width:1px;height:63px;background:rgba(255,255,255,.25)}
/* news */
.news{left:14px;top:783px;width:221px}
.news h2{font-family:"Roboto",sans-serif;font-weight:400;font-size:11px;padding-bottom:8px;border-bottom:1px solid #ddd}
.item{position:relative;height:75px;margin-top:15px}
.item .thumb{position:absolute;left:0;top:0;width:52px;height:57px;background:linear-gradient(135deg,#7f6f6a,#3b3540)}
.item .body{position:absolute;left:60px;top:0}
.item h4{font-family:"Roboto",sans-serif;font-weight:400;font-size:8px}
.item .date{font-size:7px;color:var(--blue);margin:8px 0 4px}
.item p{font-size:6px;line-height:11px;color:var(--muted);width:161px}
.feature{top:778px;width:145px}
.feature .head{height:27px;color:var(--white);font-family:"Roboto",sans-serif;font-size:8.5px;text-align:center;line-height:27px}
.feature .photo{height:97px}
.feature p{font-size:6.8px;line-height:13px;color:var(--muted);text-align:center;margin-top:13px;width:160px}
/* footer */
.footer{left:0;top:977px;width:586px;height:163px;background:var(--footer);color:var(--footer-text)}
.footer h5{position:absolute;top:25px;font-family:"Roboto",sans-serif;font-weight:400;font-size:8.5px;color:#ddd}
.f-nav{position:absolute;left:28px;top:42px;list-style:none;font-size:6.8px;line-height:13.6px}
.f-nav li::before{content:"▸";font-size:5px;margin-left:-9px;margin-right:5px}
.f-contact{position:absolute;left:140px;top:42px;font-size:7px;line-height:11px}
.f-contact .row{display:flex;align-items:center;gap:6px;margin-top:4px}
.f-contact .big{font-size:10px;color:#ddd}
.in{position:absolute;left:285px;width:153px;height:23px;background:#1c1c1c;border:1px solid #444;font-size:6px;color:#666;text-align:center;line-height:22px}
.signup{position:absolute;left:285px;top:107px;width:153px;height:22px;background:var(--green);color:#fff;font-size:7.5px;text-align:center;line-height:22px;font-family:"Roboto",sans-serif}
.social{position:absolute;left:500px;top:42px;list-style:none;font-size:7px;line-height:16.5px}
.social li{display:flex;align-items:center;gap:7px}
.social li::before{content:"";width:5px;height:5px;border-radius:50%;background:#9a9a9a}
.copy{left:0;top:1140px;width:586px;height:36px;text-align:center;font-size:6px;line-height:36px;color:#333}
</style>
</head>
<body>
<div class="page">
  <header>
    <div class="abs brand"><span class="brand-mark"></span><span class="brand-name">SUMMIT SAFETY ACADEMY</span></div>
    <svg class="abs phone-icon" width="24" height="24" viewBox="0 0 24 24"><circle cx="12" cy="12" r="11" fill="none" stroke="#1f2a7c" stroke-width="1"/><path d="M9 7.5c.6 0 1.5 2 1.3 2.5l-.9.9c.6 1.4 1.8 2.6 3.2 3.2l.9-.9c.5-.2 2.5.7 2.5 1.3 0 .8-1 2-2 2-3.6-.3-6.8-3.5-7-7 0-1 1.2-2 2-2z" fill="#1f2a7c"/></svg>
    <div class="abs contact-top"><div class="ph">Ph: 916-555-0187</div><div class="em">info@summitsafetyacademy.com</div></div>
    <div class="abs search">Search<svg width="8" height="8" viewBox="0 0 10 10"><circle cx="4" cy="4" r="3" fill="none" stroke="#333" stroke-width="1.5"/><path d="M6.3 6.3 9 9" stroke="#333" stroke-width="1.5"/></svg></div>
    <nav class="abs nav"><span>Home</span><span>About Us</span><span>Class Calender</span><span>Classes for Groups</span><span>Certification Classes</span><span>Policies</span><span>Contact</span></nav>
  </header>

  <aside class="abs appt">
    <h2>REQUEST AN APPOINTMENT</h2>
    <address>Summit Safety Academy!<br>4820 Birchwood Ave #310</address>
    <div class="field">Your Name</div>
    <div class="field">E -mail</div>
    <div class="field">Phone No</div>
    <div class="field">mm/dd/yy</div>
    <div class="field">Subjects</div>
    <div class="btn">REQUEST AN APPOINTMENT</div>
  </aside>

  <section class="abs hero" role="img" aria-label="Classroom of students attending a CPR lecture with an instructor at the front">
    <div class="abs hero-title"><div class="l1">CPR &amp; First</div><div class="l2">Aid Certification Classes</div></div>
    <div class="abs arrows"><span></span><span></span></div>
  </section>

  <section class="abs welcome">
    <h1>Welcome To <span>Summit Safety Academy!</span></h1>
    <p>Vestibulum commodo volutpat a, convallis ac, laoreet enim. Phasellus fermentum in, dolor pellentesque. Mulla imperdiet sit amet magna. Vestibulum dapibus, Vestibulum commodo volutpat a, convallis ac, laoreet enim. Phasellus fermentum in, dolor pellentesque. Mulla imperdiet sit amet magna. Vestibulum dapibus, Vestibulum commodo volutpat a, convallis ac, laoreet enim. Phasellus fermentum in.</p>
  </section>

  <article class="abs card" style="left:14px">
    <div class="photo" role="img" aria-label="AED defibrillator unit on a table in a training room" style="background:linear-gradient(135deg,#9aa0a6,#5a6068)"></div>
    <h3>GROUP CPR+AED</h3>
    <p>Lorem ipsum dolor sit amet, consec teer adipiscing, vestibulum molestie la my hendrerit. mauris haselllus. Porta. Lorem ipsum dolor sit amet,</p>
  </article>
  <article class="abs card" style="left:204px">
    <div class="photo" role="img" aria-label="Workers practicing first aid on a colleague outdoors" style="background:linear-gradient(135deg,#6f7580,#3c4048)"></div>
    <h3>GROUP CPR+FIRST AID</h3>
    <p>Lorem ipsum dolor sit amet, consec teer adipiscing, vestibulum molestie la my hendrerit. mauris haselllus. Porta. Lorem ipsum dolor sit amet,</p>
  </article>
  <article class="abs card" style="left:395px">
    <div class="photo" role="img" aria-label="Healthcare staff in scrubs practicing life support" style="background:linear-gradient(135deg,#b9c0d8,#7480b8)"></div>
    <h3>GROUP BLS/HEALTHCARE CPR</h3>
    <p>Lorem ipsum dolor sit amet, consec teer adipiscing, vestibulum molestie la my hendrerit. mauris haselllus. Porta. Lorem ipsum dolor sit amet,</p>
  </article>

  <section class="abs spec">
    <div class="photo" role="img" aria-label="Infant CPR training manikins on a classroom table"></div>
    <div class="script">Our<span style="color:#fff">Specialities</span></div>
    <div class="col" style="left:332px"><b>CPR</b><div>$39<br>Adult/Child/Infant<br>90 Minutes!</div></div>
    <div class="sep"></div>
    <div class="col" style="left:463px"><b>BLS</b><div>$49<br>Healthcare/Dental<br>90 Minutes!</div></div>
  </section>

  <section class="abs news">
    <h2>OUR NEWS</h2>
    <div class="item">
      <div class="thumb" role="img" aria-label="Trainee practicing chest compressions"></div>
      <div class="body"><h4>Sed ut perspiciatis unde omnis</h4><div class="date">22 - FEB - 2015</div><p>Praesent vestibulum molestie lacus. Aenean nmmy hendrerit mauris. Phasellus porta. Fusce suscrius mi. Praesent vestibulum molestie</p></div>
    </div>
    <div class="item">
      <div class="thumb" role="img" aria-label="Instructor demonstrating on a manikin"></div>
      <div class="body"><h4>Sed ut perspiciatis unde omnis</h4><div class="date">22 - FEB - 2015</div><p>Praesent vestibulum molestie lacus. Aenean nmmy hendrerit mauris. Phasellus porta. Fusce suscrius mi. Praesent vestibulum molestie</p></div>
    </div>
  </section>

  <section class="abs feature" style="left:258px">
    <div class="head" style="background:var(--blue)">ONSITE-WE COME TO YOU</div>
    <div class="photo" role="img" aria-label="Rescuer performing CPR on a person lying on a street" style="background:linear-gradient(180deg,#8c9a7a,#6d6f6a)"></div>
    <p>Lorem ipsum dolor sit amet, consectetur adipiscing elit. Sed blandit massa vel mauris sollicitudin dignissim.</p>
  </section>
  <section class="abs feature" style="left:425px">
    <div class="head" style="background:var(--green)">HOSTED-WE OFFER WEEKLY</div>
    <div class="photo" role="img" aria-label="Weekly class seated in a bright training room" style="background:linear-gradient(180deg,#e2e6ea,#8d7f78)"></div>
    <p>Lorem ipsum dolor sit amet, consectetur adipiscing elit. Sed blandit massa vel mauris sollicitudin dignissim.</p>
  </section>

  <footer class="abs footer">
    <h5 style="left:18px">NAVIGATION</h5>
    <ul class="f-nav"><li>Class Calender</li><li>Classes for Groups</li><li>Group CPR+AED</li><li>Group CPR+First Aid</li><li>Group BLS/Healthcare CPR</li><li>Certification Classes</li><li>About Us</li></ul>
    <h5 style="left:138px">CONTACT US</h5>
    <div class="f-contact">Summit Safety Academy!<br>4820 Birchwood Ave #310
      <div class="row"><svg width="10" height="10" viewBox="0 0 10 10"><path d="M2 1c.5 0 1.2 1.5 1 2l-.6.6c.5 1 1.3 1.8 2.3 2.3l.6-.6c.4-.2 2 .5 2 1 0 .6-.8 1.5-1.5 1.5C3.3 7.6 1.2 5.5 1 2.7 1 2 1.5 1 2 1z" fill="#ddd"/></svg><span class="big">916-555-0187</span></div>
      <div class="row"><svg width="10" height="8" viewBox="0 0 10 8"><rect x=".5" y=".5" width="9" height="7" fill="none" stroke="#ddd"/><path d="M.5.5 5 4.5 9.5.5" fill="none" stroke="#ddd"/></svg><span style="color:#ddd">info@summitsafetyacademy.com</span></div>
    </div>
    <h5 style="left:288px">SIGN UP FOR NEWSLETTER</h5>
    <div class="in" style="top:54px">Enter Name</div>
    <div class="in" style="top:84px">Email</div>
    <div class="signup">SIGN UP NOW</div>
    <h5 style="left:500px">SOCIAL MEDIA</h5>
    <ul class="social"><li>Linkhall</li><li>Chirpwire</li><li>Groupsphere</li><li>Clipstream</li></ul>
  </footer>
  <div class="abs copy">©2014 - 2015 SUMMIT SAFETY ACADEMY!. ALL RIGHTS RESERVED.</div>
</div>
</body>
</html>
```